New Business Card Design Project

I need a design for business cards, i am an electrical business called "Corvane Electrical and Communications" i need the cards to be double sided with the company logo on the back (attached) the front needs to say my company name, web site, email address, telephone number, and ABN number and electrical license number. I am open to different arrangements of the information but would like the background to be incorporating something electrical or something that looks smart. open to all additional ideas also.

The company colours are orange and grey see logo attached.

Business Name: Corvane Electrical and Communications
Website: corvaneelectricalandcomms.example.com.au
Email: brent@corvaneelectricalandcomms.example.com.au
Telephone(mobile): 0481209736
ABN: 71208349162
Lic No: 418273D

Target Market(s)

Business entities, Project Managers, Accounts, Clients

Industry/Entity Type

Electrician

Contact Information for Business Card

I need a design for business cards, i am an electrical business called "Corvane Electrical and Communications" i need the cards to be double sided with the company logo on the back (attached) the front needs to say my company name

Font styles to use
Serif
Sans Serif

Colors
f37122
5c5c5c

Requirements
Must have
• Must have the Logo on the back open to different ways of it being on the back but had in mind to keep it central but again open to other options
Nice to have
• A real modern cool background that is eye catching yet contemporary
Should not have
• No backgrounds of a light bulb or plug or anything like that

```html
<!DOCTYPE html>
<html lang="en">
<head>
<meta charset="utf-8">
<title>Corvane Electrical and Communications – Business Card</title>
<link rel="stylesheet" href="https://fonts.googleapis.com/css2?family=Exo+2:wght@600;700&family=Open+Sans:wght@300;600&display=swap">
<style>
  :root {
    --brand-orange: #f37122;
    --brand-orange-light: #f58a3f;
    --brand-orange-deep: #d9601a;
    --brand-grey: #5c5c5c;
    --card-dark: #2a2a2c;
    --card-mid: #48484b;
    --text-light: #d6d6d6;
    --text-muted: #b9b9bc;
    --page-bg: #e9e9ea;
    --tag-text: #1e1e1e;
  }
  html, body {
    margin: 0;
    padding: 0;
    width: 1200px;
    height: 969px;
    overflow: hidden;
    background: var(--page-bg);
  }
  .canvas {
    position: relative;
    width: 1200px;
    height: 969px;
  }
  .business-card {
    position: absolute;
    left: 100px;
    top: 200px;
    width: 1000px;
    height: 568px;
    border-radius: 34px;
    overflow: hidden;
    background:
      radial-gradient(ellipse at 20% 15%, rgba(255,255,255,0.10), transparent 55%),
      linear-gradient(160deg, var(--card-mid) 0%, var(--card-dark) 55%, #333336 100%);
    box-shadow: 0 18px 40px rgba(0,0,0,0.25);
  }
  .brand-name {
    position: absolute;
    left: 52px;
    top: 84px;
    width: 540px;
    margin: 0;
    font-family: "Exo 2", sans-serif;
    font-weight: 600;
    font-size: 48px;
    line-height: 1.12;
    letter-spacing: 0.5px;
    color: var(--brand-orange);
  }
  .company-details {
    position: absolute;
    left: 41px;
    top: 312px;
    font-family: "Open Sans", sans-serif;
    font-weight: 300;
    color: var(--text-light);
  }
  .company-details p { margin: 0; }
  .detail-id {
    font-size: 25px;
    line-height: 39px;
    letter-spacing: 0.5px;
  }
  .detail-mobile {
    margin-top: 16px !important;
    font-size: 25px;
    line-height: 39px;
  }
  .detail-mobile .label {
    color: var(--brand-orange);
    font-weight: 600;
  }
  .detail-web {
    font-size: 21px;
    line-height: 39px;
    color: var(--text-muted);
  }
  .name-tag {
    position: absolute;
    left: 618px;
    top: 380px;
    width: 382px;
    height: 92px;
    background: linear-gradient(180deg, var(--brand-orange-light) 0%, var(--brand-orange) 55%, var(--brand-orange-deep) 100%);
    text-align: right;
    box-sizing: border-box;
    padding: 11px 18px 0 0;
    font-family: "Exo 2", sans-serif;
    color: var(--tag-text);
  }
  .name-tag .person-name {
    margin: 0;
    font-size: 35px;
    font-weight: 700;
    line-height: 40px;
  }
  .name-tag .person-title {
    margin: 0;
    font-size: 25px;
    font-weight: 600;
    line-height: 32px;
  }
</style>
</head>
<body>
<div class="canvas">
  <section class="business-card">
    <h1 class="brand-name">Corvane Electrical and Communications</h1>

    <div class="company-details">
      <p class="detail-id">ABN: 71208349162</p>
      <p class="detail-id">Lic No: 418273D</p>
      <p class="detail-mobile"><span class="label">Mobile :</span> 0481209736</p>
      <p class="detail-web">brent@corvaneelectricalandcomms.example.com.au</p>
      <p class="detail-web">corvaneelectricalandcomms.example.com.au</p>
    </div>

    <div class="name-tag">
      <p class="person-name">Dale Hutton</p>
      <p class="person-title">CEO/Founder</p>
    </div>
  </section>
</div>
</body>
</html>
```